Tovel & Associates - London New Letting and Property Management Company *

Tovel & Associates LTD is a new company based in London, and works with brand new residential property in the city centre.

We are aiming to have 1000 new properties a year.

We are looking for something modern and minimalistic :
Logo ,Monogram, Paper Head and Business Card.

Target Market(s)

Internation landlords

Industry/Entity Type

Real Estate

Logo Text

Tovel & Associates

Colors

Designer to choose colors to be used in the design.

Requirements
Nice to have
• A particular monogram with "TA"
Should not have
• Little House over the logo

```html
<!DOCTYPE html>
<html lang="en">
<head>
<meta charset="UTF-8">
<title>Tovel &amp; Associates – Business Card</title>
<link rel="stylesheet" href="https://fonts.googleapis.com/css2?family=Oswald:wght@500&family=Work+Sans:wght@400;500&display=swap">
<style>
  :root {
    --page-bg: #1b1b1c;
    --card-bg: #262627;
    --card-edge: #333334;
    --brand-grey: #a9abae;
    --accent-blue: #1fa3e4;
    --text-white: #f2f2f2;
  }
  * { margin: 0; padding: 0; box-sizing: border-box; }
  html, body {
    width: 1200px; height: 900px; overflow: hidden;
    background: var(--page-bg);
  }
  .canvas {
    width: 1200px; height: 900px;
    display: flex; flex-direction: column;
    align-items: center; justify-content: center; gap: 36px;
  }
  .card {
    width: 700px; height: 396px;
    background: var(--card-bg);
    border: 1px solid var(--card-edge);
    box-shadow: 0 18px 40px rgba(0,0,0,0.55);
    position: relative;
  }
  .card-front {
    display: flex; align-items: center; justify-content: center;
  }
  .brand {
    display: flex; align-items: center; gap: 16px;
    color: var(--brand-grey);
    font-family: 'Work Sans', sans-serif;
    font-weight: 500; font-size: 26px; letter-spacing: 3px;
    text-transform: uppercase;
  }
  .brand-square {
    width: 26px; height: 26px; background: var(--brand-grey);
  }
  .card-back {
    display: flex; align-items: center; justify-content: center; gap: 34px;
  }
  .identity { text-align: right; }
  .person-name {
    font-family: 'Oswald', sans-serif; font-weight: 500;
    font-size: 40px; letter-spacing: 1px; line-height: 1.05;
    color: var(--accent-blue); text-transform: uppercase;
  }
  .person-role {
    font-family: 'Work Sans', sans-serif; font-size: 18px;
    color: var(--text-white); margin-top: 4px;
  }
  .divider { width: 2px; height: 78px; background: var(--text-white); }
  .contacts { list-style: none; }
  .contacts li {
    display: flex; align-items: center; gap: 12px;
    font-family: 'Work Sans', sans-serif; font-size: 18px;
    color: var(--text-white); line-height: 1.55;
  }
  .contacts svg { width: 13px; height: 13px; flex: none; }
  .contacts .highlight { color: var(--accent-blue); }
</style>
</head>
<body>
<main class="canvas">
  <section class="card card-front">
    <div class="brand">
      <span class="brand-square"></span>
      <span>Tovel &amp; Associates</span>
    </div>
  </section>

  <section class="card card-back">
    <div class="identity">
      <h1 class="person-name">Daniel Hartley</h1>
      <p class="person-role">Director</p>
    </div>
    <div class="divider"></div>
    <ul class="contacts">
      <li>
        <svg viewBox="0 0 16 16" aria-hidden="true"><path d="M4 1.5 6.2 4 5 5.6c.9 2 2.4 3.5 4.4 4.4L11 8.8l2.5 2.2-1.3 2.5C7 13.3 2.7 9 2.5 3.8Z" fill="#1fa3e4"/></svg>
        <span>+44 20 7946 0183</span>
      </li>
      <li>
        <svg viewBox="0 0 16 16" aria-hidden="true"><rect x="1.5" y="3.5" width="13" height="9" fill="none" stroke="#1fa3e4" stroke-width="1.5"/><path d="M1.5 3.5 8 9l6.5-5.5" fill="none" stroke="#1fa3e4" stroke-width="1.5"/></svg>
        <span>info@tovel&amp;associates.com</span>
      </li>
      <li>
        <svg viewBox="0 0 16 16" aria-hidden="true"><circle cx="8" cy="8" r="6.3" fill="none" stroke="#1fa3e4" stroke-width="1.4"/><ellipse cx="8" cy="8" rx="2.6" ry="6.3" fill="none" stroke="#1fa3e4" stroke-width="1.2"/><path d="M1.7 8h12.6" stroke="#1fa3e4" stroke-width="1.2"/></svg>
        <span>www.<span class="highlight">tovel&amp;associates</span>.com</span>
      </li>
    </ul>
  </section>
</main>
</body>
</html>
```